Modern looking signage for dental office.

Exterior signage for passing cars
Updates
Need extra days to review
Target Market(s)
Cars passing by
Font styles to use
Sans Serif
Colors
3276b5
Requirements
Must have
- Logo
- OPEN ON SUTURDAY AND SUNDAY
- NIGHT CLINIC AVAILABLE
- PLEASE USE THE FONT TYPE IN FILE 4 UPLOADED BELOW.
- (847) 302-7469
- Modern looking

```html
<!DOCTYPE html>
<html lang="en">
<head>
<meta charset="utf-8">
<title>Brightway Dental – Exterior Sign</title>
<link href="https://fonts.googleapis.com/css2?family=Saira:wght@500;600&family=Saira+Semi+Condensed:wght@400;500&display=swap" rel="stylesheet">
<style>
  :root {
    --brand-blue: #0b5aa0;
    --accent-blue: #3276b5;
    --ink: #1c1c1c;
    --charcoal: #3a3a3a;
    --stripe: #4a4a4a;
    --panel: #ffffff;
    --backdrop: #eef0f2;
  }
  * { margin: 0; padding: 0; box-sizing: border-box; }
  html, body {
    width: 1200px; height: 1200px; overflow: hidden;
    background: var(--backdrop);
  }
  .sign {
    position: absolute; left: 50px; top: 290px;
    width: 1100px; height: 620px;
    background: var(--panel);
    box-shadow: 0 8px 30px rgba(0,0,0,0.12);
    overflow: hidden;
  }
  .sign-art { display: block; }
  .brand-circle { fill: none; stroke: var(--charcoal); stroke-width: 4; }
  .brand-name {
    font-family: "Saira Semi Condensed", sans-serif;
    font-weight: 500; font-size: 64px; fill: var(--charcoal);
    letter-spacing: 1px;
  }
  .brand-tagline {
    font-family: "Saira Semi Condensed", sans-serif;
    font-weight: 400; font-size: 30px; fill: var(--charcoal);
  }
  .offer-headline {
    font-family: "Saira", sans-serif;
    font-weight: 600; font-size: 60px; fill: #fff;
  }
  .offer-days {
    font-family: "Saira", sans-serif;
    font-weight: 500; font-size: 27px; fill: #fff;
  }
  .phone {
    font-family: "Saira", sans-serif;
    font-weight: 600; font-size: 58px; fill: var(--ink);
  }
  .edge-stripe { fill: var(--stripe); }
  .offer-band { fill: var(--brand-blue); }
</style>
</head>
<body>
  <section class="sign">
    <svg class="sign-art" width="1100" height="620" viewBox="0 0 1100 620" role="group" aria-label="Brightway Dental exterior sign">
      <polygon class="offer-band" points="0,430 1100,300 1100,420 0,550"/>
      <rect class="edge-stripe" x="1032" y="0" width="28" height="470"/>
      <rect class="edge-stripe" x="1066" y="0" width="6" height="460"/>

      <g class="brand">
        <circle class="brand-circle" cx="320" cy="150" r="95"/>
        <text class="brand-name" x="445" y="180" textLength="560" lengthAdjust="spacingAndGlyphs">BRIGHTWAY DENTAL</text>
        <text class="brand-tagline" x="1005" y="232" text-anchor="end">MODERN GENERAL DENTISTRY</text>
      </g>

      <g class="offer" transform="translate(550,425) rotate(-6.74)">
        <text class="offer-headline" x="-10" y="10" text-anchor="middle">Night Clinic Available</text>
        <text class="offer-days" x="350" y="44" text-anchor="end">Open on Saturday and Sunday</text>
        <text class="phone" x="-30" y="122" text-anchor="middle">(847) 302-7469</text>
      </g>
    </svg>
  </section>
</body>
</html>
```